4D Cradle Glimpse Luxury Ultrasound Billboard

Design a HIGH-END, MODERN billboard for my private prenatal ultrasound studio, 4D Cradle Glimpse, located in Pace, Florida.
This billboard will be viewed by drivers traveling at highway speeds, so it must be extremely clean, simple, and readable within 6 seconds.
About My Business
4D Cradle Glimpse is a private prenatal ultrasound studio specializing in:
Highest technology 4D/HD Ultrasounds
Early Gender Determination
Pregnancy Confirmation
I have been serving families for nearly 10 years and is known for creating a memorable experience, not just an ultrasound appointment.
Design Style
I DO NOT want:
Flowers
Leaves
Swirls
Glitter
Hearts everywhere
Busy backgrounds
Generic maternity stock graphics
I DO want:
Modern
Luxury
Upscale
Clean
Professional
Eye-catching
Premium medical spa feel
Colors
Use colors from my logo:
LOGO Green ( or a deep green)
Black
White
Soft Gold accents
Images:
Incorporate my professional headshot in a clean, modern way, logo, and the ultrasound images
Text
Keep wording minimal.
Primary Headline ( OPEN TO IDEAS) :
EXAMPLES ( WOULD RATHER SOMETHING MORE CATCHY)
" ADVANCED IMAGING. UNFORGETTABLE MOMENTS"
"MEET YOUR BABY BEFORE BIRTH"
Under headline:
4D Ultrasound • Early Gender • Pregnancy Confirmation
Business Name:
4D Cradle Glimpse
Private Prenatal Ultrasound Studio
Phone Number:
850-471-5923
Important
This billboard must be readable in 5–6 seconds from a moving vehicle.
Less text is better.
The phone number and business name must be visible from a distance.
The design should feel like a premium brand that immediately tells expecting parents:
“This is where I go to see my baby.”
Files Provided
Official logo
Headshot
Ultrasound images
Don’t make this look like a medical office billboard.
Make it look like a luxury baby experience billboard. That’s what separates 4D Cradle Glimpse from hospitals, OB offices, and all the new studios popping up around you. The emotional connection is what gets moms to book. ❤️
Billboard Size - 10.6” x 36”

```html
<!DOCTYPE html>
<html lang="en">
<head>
<meta charset="utf-8">
<title>4D Cradle Glimpse Billboard</title>
<link rel="stylesheet" href="https://fonts.googleapis.com/css2?family=Playfair+Display:wght@900&family=Poppins:wght@500;600&family=Roboto+Condensed:wght@700&display=swap">
<style>
  :root {
    --gold: #d8a43c;
    --cream: #f8efc4;
    --ink: #1f2b22;
    --logo-gold: #c9973a;
    --page: #ecebe7;
    --photo-left-a: #e2c6a8;
    --photo-left-b: #c9785f;
    --photo-right-a: #e7dcc9;
    --photo-right-b: #3f5a3c;
  }
  * { margin: 0; padding: 0; box-sizing: border-box; }
  html, body { width: 1200px; height: 829px; overflow: hidden; background: var(--page); }
  .billboard {
    position: absolute; left: 0; top: 238px; width: 1200px; height: 353px;
    background: var(--gold); overflow: hidden;
  }
  .ultrasound-photo {
    position: absolute; left: 0; top: 0; width: 300px; height: 353px;
    background: radial-gradient(circle at 45% 32%, var(--photo-left-b) 0 28%, transparent 29%),
                linear-gradient(160deg, var(--photo-left-a), var(--gold) 70%);
  }
  .headshot-photo {
    position: absolute; right: 0; top: 0; width: 235px; height: 353px;
    background: linear-gradient(180deg, var(--photo-right-a) 0%, var(--photo-right-b) 100%);
  }
  .spotlight {
    position: absolute; left: 292px; top: -130px; width: 640px; height: 620px;
    border-radius: 50%; background: var(--cream);
  }
  .content { position: absolute; left: 0; top: 0; width: 1200px; height: 353px; }
  .content > * { white-space: nowrap; }
  .brand {
    position: absolute; left: 412px; top: 18px; width: 400px; text-align: center;
    font: 600 24px/1 "Poppins", sans-serif; color: var(--logo-gold);
  }
  .tagline {
    position: absolute; left: 412px; top: 52px; width: 400px; text-align: center;
    font: 500 15px/1 "Poppins", sans-serif; color: var(--ink);
  }
  .headline {
    position: absolute; left: 292px; top: 74px; width: 640px; text-align: center;
    font: 900 80px/1 "Playfair Display", serif; color: var(--ink); letter-spacing: -1px;
  }
  .services {
    position: absolute; left: 292px; top: 180px; width: 640px; text-align: center;
    font: 500 19px/1 "Poppins", sans-serif; color: var(--ink);
  }
  .phone {
    position: absolute; left: 362px; top: 222px; display: flex; align-items: center; gap: 18px;
  }
  .phone-icon { width: 44px; height: 44px; flex: none; }
  .phone-number {
    font: 700 78px/1 "Roboto Condensed", sans-serif; color: var(--ink); letter-spacing: 1px;
  }
</style>
</head>
<body>
  <div class="billboard">
    <div class="ultrasound-photo" role="img" aria-label="4D ultrasound image of a baby above a probe on a pregnant belly"></div>
    <div class="spotlight"></div>
    <div class="headshot-photo" role="img" aria-label="Headshot of the studio sonographer holding an ultrasound probe"></div>
    <div class="content">
      <div class="brand">4D Cradle Glimpse</div>
      <div class="tagline">Private Prenatal Ultrasound Studio</div>
      <div class="headline">Meet your baby</div>
      <div class="services">• 4D Ultrasound • Early Gender • Pregnancy Confirmation</div>
      <div class="phone">
        <svg class="phone-icon" viewBox="0 0 44 44" aria-hidden="true">
          <circle cx="22" cy="22" r="22" fill="var(--gold)"/>
          <path d="M15 12c1-1 2.5-1 3.3.2l2 3c.6 1 .4 2.2-.4 3l-1.4 1.3c1 2.3 2.8 4.2 5.1 5.2l1.3-1.4c.8-.8 2-1 3-.4l3 2c1.2.8 1.2 2.3.2 3.3l-1.6 1.6c-1.3 1.3-3.3 1.6-5 .8-5-2.4-9-6.4-11.4-11.4-.8-1.7-.5-3.7.8-5z" fill="var(--ink)"/>
        </svg>
        <span class="phone-number">850 471 5923</span>
      </div>
    </div>
  </div>
</body>
</html>
```